Meridale Staffing Website

My business has been word of mouth over the last 3 years and has grown. Now I need a website for additional marketing as we have new clients asking for a website.

You have already completed my Logo during an earlier project. I have attached the logo.

We do Staff Augmentation and Operation Support.

What is that?
Staff augmentation is an outsourcing strategy that allows companies to fill specific, temporary roles to achieve business objectives. This staffing method complements existing teams with specific talent, enhancing business capabilities or filling gaps left by members on extended leave.

We work alongside the internal recruiting team to assist clients to meet and exceed financial goals.

```html
<!DOCTYPE html>
<html lang="en">
<head>
<meta charset="utf-8">
<title>Meridale Staffing</title>
<link rel="stylesheet" href="https://fonts.googleapis.com/css2?family=Montserrat:wght@400;500;600;700;800;900&display=swap">
<style>
:root{
  --navy:#0f3f68;
  --navy-deep:#0a2f52;
  --navy-mid:#1c5480;
  --grey:#6b6b6b;
  --grey-light:#8a8a8a;
  --text:#333;
  --muted:#7a7a7a;
  --white:#fff;
  --sky:#2c9be0;
}
*{box-sizing:border-box;margin:0;padding:0}
html,body{width:1200px;height:3610px;overflow:hidden}
body{position:relative;background:var(--white);font-family:"Montserrat",sans-serif;color:var(--text)}
.abs{position:absolute}

/* header */
.brand{left:143px;top:22px;display:flex;align-items:center;gap:14px}
.brand-dot{width:62px;height:62px;border-radius:50%;background:var(--navy)}
.brand-name{font-weight:700;font-size:30px;line-height:1;color:var(--navy);letter-spacing:.5px}
.nav{left:515px;top:47px;display:flex;gap:30px;font-weight:600;font-size:15px;color:#222}
.nav .active{color:var(--navy)}
.search-btn{left:1006px;top:30px;width:50px;height:54px;background:var(--navy);border-radius:4px 26px 4px 26px;display:flex;align-items:center;justify-content:center}

/* hero */
.hero{left:0;top:118px;width:1200px;height:780px}
.hero-badge{left:143px;top:268px;width:468px;height:468px;border-radius:50%;background:rgba(24,78,118,.92);text-align:center;color:var(--white)}
.hero-title{margin-top:96px;font-weight:800;font-size:39px;line-height:47px;text-transform:uppercase}
.btn-slant{display:inline-block;font-weight:700;color:var(--white);font-size:15px;text-transform:uppercase}
.hero-cta{left:262px;top:578px;width:230px;height:70px}
.hero-cta span{position:absolute;left:0;top:0;width:100%;line-height:70px;text-align:center}
.hero-dots{left:1116px;top:472px;display:flex;flex-direction:column;gap:11px}
.hero-dots i{width:9px;height:9px;border-radius:50%;background:var(--white);display:block}
.mouse{left:577px;top:858px;width:46px;height:56px;border-radius:23px 23px 8px 8px;background:var(--white);display:flex;justify-content:center;align-items:center}
.mouse b{width:18px;height:30px;border:2.5px solid #111;border-radius:9px;display:block;position:relative}
.mouse b::after{content:"";position:absolute;left:5.5px;top:5px;width:2.5px;height:7px;background:#111;border-radius:2px}

/* about */
.about-title{left:160px;top:968px;font-weight:800;font-size:52px;color:var(--navy);line-height:1}
.about-sub{left:160px;top:1034px;font-weight:700;font-size:39px;color:#5e5e5e;line-height:1}
.about-text{left:160px;top:1098px;width:448px;font-size:13.6px;line-height:24px;color:#444;text-align:justify}
.about-cta{left:160px;top:1297px;width:214px;height:58px}
.about-cta span{position:absolute;left:0;top:0;width:100%;line-height:58px;text-align:center}
.about-mark{left:683px;top:995px;width:362px;height:362px;border-radius:50%;background:radial-gradient(circle at 45% 40%,#24557e,#0a2a48 70%);display:flex;align-items:center;justify-content:center;color:var(--white);font-weight:700;font-size:30px;text-align:center;line-height:1.2}

/* services */
.service{top:1463px;width:582px;height:482px;display:flex;align-items:flex-end;justify-content:center;padding-bottom:78px;color:var(--white);font-weight:800;font-size:40px;line-height:52px;text-align:center;text-transform:uppercase}
.service-staff{left:12px;border-radius:40px 62px 72px 0;background:radial-gradient(circle at 62% 30%,#8fd0ff 0,#2f7fc4 18%,#144b85 45%,#0c3160 80%)}
.service-ops{left:606px;border-radius:72px 62px 0 72px;background:linear-gradient(160deg,#6f6f6f,#3f3f3f 45%,#2b2b2b)}
.service-pointer{left:287px;top:1944px;width:0;height:0;border-left:16px solid transparent;border-right:16px solid transparent;border-top:16px solid #0c3160}

.features{left:0;top:2020px;width:1200px}
.feature{position:absolute;width:240px;text-align:center;font-weight:700;font-size:15.5px;line-height:25px;color:#222;text-transform:uppercase}
.feature-ring{margin:0 auto 12px;width:172px;height:172px;border-radius:50%;border:3px solid var(--navy);display:flex;align-items:center;justify-content:center}
.feature-ring>div{width:158px;height:158px;border-radius:50%;border:7px solid var(--grey);display:flex;align-items:center;justify-content:center}

/* news */
.news-bg{left:0;top:2250px;width:1200px;height:820px;background:linear-gradient(180deg,#fff 0%,#eef3f8 30%,#f3f6fa 70%,#fff 100%)}
.news-title{left:0;top:2375px;width:1200px;text-align:center;font-weight:800;font-size:52px;color:var(--navy);line-height:1}
.news-title span{color:#6a6a6a}
.news-grid{left:143px;top:2484px;width:913px;height:492px;display:grid;grid-template-columns:repeat(3,1fr);grid-template-rows:repeat(2,1fr);border:1px solid #dfe4ea;background:var(--white)}
.news-card{display:flex;flex-direction:column;align-items:center;padding:30px 26px 0;text-align:center;background:var(--white)}
.news-card h3{font-weight:600;font-size:16.5px;color:#222;text-transform:uppercase}
.news-date{margin-top:16px;font-size:12.5px;color:var(--navy)}
.news-card p{margin-top:12px;font-size:13px;line-height:22px;color:var(--muted)}
.news-more{margin-top:22px;font-weight:700;font-size:13.5px;color:var(--navy);display:flex;align-items:center;gap:8px}
.news-photo-a{background:linear-gradient(180deg,#9db4cf,#6d7d9c 55%,#c07a8e)}
.news-photo-b{background:linear-gradient(135deg,#b7c6d6,#6f8fb0 55%,#a6b9cc)}
.news-photo-c{background:linear-gradient(160deg,#1d3552,#2d4d6e 50%,#0f1f33)}

/* contact */
.contact{left:10px;top:3065px;width:1180px;height:545px;border-radius:70px 0 0 0;background:linear-gradient(180deg,#0f4474,#0c3a66)}
.contact-title{left:0;top:3140px;width:1200px;text-align:center;font-weight:800;font-size:52px;color:var(--white);line-height:1}
.contact-label{font-size:15.5px;color:var(--white)}
.field{position:absolute;background:var(--white);border:1px solid #c8d2dc;font-size:10px;color:#555;padding:8px 10px;text-transform:uppercase}
.submit{left:608px;top:3450px;width:80px;height:28px;border-radius:14px;background:#5f6770;color:var(--white);font-weight:700;font-size:10.5px;display:flex;align-items:center;justify-content:center}
.info{left:757px;display:flex;align-items:center;gap:16px;color:var(--white);font-size:11.5px;line-height:17px}
.info-icon{width:34px;height:34px;border-radius:50%;border:1.5px solid var(--white);display:flex;align-items:center;justify-content:center;flex-shrink:0}
.socials{left:760px;top:3448px;display:flex;gap:12px}
.socials i{width:22px;height:22px;border-radius:50%;display:block;background:#1b5a93}
.socials i:nth-child(2){background:#2d9fe8}
.socials i:nth-child(3){background:#e3262d}
.socials i:nth-child(4){background:#b98a3b}
.socials i:nth-child(5){background:#1b5a93}
.live-chat{left:1137px;top:3410px;width:34px;height:96px;border-radius:20px 0 0 20px;background:var(--sky);color:var(--white);font-weight:700;font-size:10px;display:flex;align-items:center;justify-content:center}
.live-chat span{transform:rotate(-90deg);white-space:nowrap}
.footer-rule{left:143px;top:3532px;width:913px;height:1px;background:rgba(255,255,255,.2)}
.copyright{left:0;top:3563px;width:1200px;text-align:center;font-size:11.5px;color:var(--white)}
</style>
</head>
<body>

<header>
  <div class="abs brand"><span class="brand-dot"></span><span class="brand-name">MERIDALE<br>STAFFING</span></div>
  <nav class="abs nav">
    <span class="active">HOME</span><span>ABOUT</span><span>SERVICES</span><span>NEWS</span><span>CONTACT</span>
  </nav>
  <div class="abs search-btn">
    <svg width="16" height="16" viewBox="0 0 16 16"><circle cx="6.5" cy="6.5" r="4.5" fill="none" stroke="#fff" stroke-width="2"/><line x1="10" y1="10" x2="14" y2="14" stroke="#fff" stroke-width="2.4" stroke-linecap="round"/></svg>
  </div>
</header>

<section class="abs hero">
  <svg width="1200" height="780" viewBox="0 118 1200 780" role="img" aria-label="Business team working around a glowing holographic globe">
    <defs>
      <radialGradient id="heroFill" cx="70%" cy="55%" r="70%">
        <stop offset="0" stop-color="#2f7fd0"/>
        <stop offset=".35" stop-color="#163f6e"/>
        <stop offset=".75" stop-color="#0c1d33"/>
        <stop offset="1" stop-color="#070f1c"/>
      </radialGradient>
    </defs>
    <path d="M18,887 L18,520 C18,280 160,125 430,125 L1190,125 L1190,540 C1190,760 1060,876 820,887 Z" fill="url(#heroFill)"/>
    <path d="M8,560 C8,270 170,118 440,118 L1190,118" fill="none" stroke="#0f3f68" stroke-width="12"/>
    <path d="M1198,300 L1198,540 C1198,770 1060,884 820,887" fill="none" stroke="#6b6b6b" stroke-width="12"/>
  </svg>
</section>
<div class="abs hero-badge"><h1 class="hero-title">We do staff<br>augmentation<br>and operation<br>support</h1></div>
<div class="abs hero-cta">
  <svg width="230" height="70" viewBox="0 0 230 70"><path d="M0,70 L28,16 C34,5 44,0 58,0 L230,0 L202,54 C196,65 186,70 172,70 Z" fill="#6b6b6b"/></svg>
  <span class="btn-slant">Get Started</span>
</div>
<div class="abs hero-dots"><i></i><i></i><i></i></div>
<div class="abs mouse"><b></b></div>

<section>
  <h2 class="abs about-title">ABOUT</h2>
  <p class="abs about-sub">MERIDALE STAFFING</p>
  <p class="abs about-text">Lorem ipsum dolor sit amet, consectetur adipiscing elit, sed do eiusmod tempor incididunt ut labore et dolore magna aliqua. Quis ipsum suspendisse ultrices gravida. Risus commodo viverra maecenas accumsan lacus vel facilisis. Lorem ipsum dolor sit amet, consectetur adipiscing elit, sed do eiusmod tempor incididunt ut labore et dolore magna suspendisse ultrices gravidommodo viverra maecenas accumsan lacus vel facilisis.</p>
  <div class="abs about-cta">
    <svg width="214" height="58" viewBox="0 0 214 58"><path d="M0,58 L24,14 C29,5 38,0 50,0 L214,0 L190,44 C185,53 176,58 164,58 Z" fill="#0f3f68"/></svg>
    <span class="btn-slant">Read More</span>
  </div>
  <div class="abs about-mark" role="img" aria-label="Meridale Staffing name over a dark blue network backdrop">Meridale<br>Staffing</div>
</section>

<section>
  <div class="abs service service-staff" role="img" aria-label="Staff augmentation: people connected across a glowing globe"><span>Staff<br>augmentation</span></div>
  <div class="abs service service-ops" role="img" aria-label="Operation support: team in a monitoring room with world map screens"><span>Operation<br>support</span></div>
  <div class="abs service-pointer"></div>

  <div class="abs features">
    <svg class="abs" style="left:82px;top:65px" width="36" height="66" viewBox="0 0 36 66"><path d="M33,2 L3,33 L33,64" fill="none" stroke="#9aa3ad" stroke-width="1.5"/></svg>
    <svg class="abs" style="left:1082px;top:65px" width="36" height="66" viewBox="0 0 36 66"><path d="M3,2 L33,33 L3,64" fill="none" stroke="#9aa3ad" stroke-width="1.5"/></svg>

    <div class="feature" style="left:112px">
      <div class="feature-ring"><div>
        <svg width="84" height="84" viewBox="0 0 84 84" fill="none" stroke="#0f3f68" stroke-width="2.5" stroke-linejoin="round"><rect x="30" y="10" width="36" height="34"/><path d="M42 38V20M37 25l5-5 5 5M54 38V20M49 25l5-5 5 5"/><rect x="6" y="50" width="10" height="24"/><path d="M16 54h18c4 0 6 4 2 6H26M16 70l28 2 30-18c3-2 0-6-3-5L50 58"/></svg>
      </div></div>
      Handling of<br>work projects
    </div>
    <div class="feature" style="left:358px">
      <div class="feature-ring"><div>
        <svg width="84" height="84" viewBox="0 0 84 84" fill="none" stroke="#0f3f68" stroke-width="3"><circle cx="48" cy="36" r="22"/><circle cx="48" cy="36" r="15"/><path d="M41 36l5 5 9-10"/><path d="M32 52L12 72" stroke-width="7" stroke-linecap="round"/></svg>
      </div></div>
      Background<br>verification
    </div>
    <div class="feature" style="left:603px">
      <div class="feature-ring"><div>
        <svg width="84" height="84" viewBox="0 0 84 84" fill="none" stroke="#0f3f68" stroke-width="2.5"><path d="M14 32V10M9 15l5-5 5 5M34 28V6M29 11l5-5 5 5M50 28V6M45 11l5-5 5 5M70 32V10M65 15l5-5 5 5"/><circle cx="24" cy="46" r="6"/><circle cx="42" cy="46" r="6"/><circle cx="60" cy="46" r="6"/><path d="M12 66c0-8 6-12 12-12s12 4 12 12M30 66c0-8 6-12 12-12s12 4 12 12M48 66c0-8 6-12 12-12s12 4 12 12M12 66h60"/></svg>
      </div></div>
      Performance<br>management
    </div>
    <div class="feature" style="left:848px">
      <div class="feature-ring"><div>
        <svg width="84" height="84" viewBox="0 0 84 84" fill="none" stroke="#0f3f68" stroke-width="2.5"><rect x="52" y="8" width="18" height="24"/><path d="M56 14v12"/><path d="M12 40c10-4 20-10 30-14l6 10-20 12"/><circle cx="44" cy="54" r="8"/><circle cx="44" cy="54" r="3"/><circle cx="64" cy="60" r="6"/><circle cx="64" cy="60" r="2"/><path d="M10 60l14 10"/></svg>
      </div></div>
      Feedback<br>mechanism
    </div>
  </div>
</section>

<section>
  <div class="abs news-bg" role="img" aria-label="Faded photo of business people in an office"></div>
  <h2 class="abs news-title">LATEST <span>NEWS</span></h2>
  <div class="abs news-grid">
    <div class="news-photo-a" role="img" aria-label="Silhouettes of business people against a city skyline"></div>
    <article class="news-card">
      <h3>At vero eos eaccusamu</h3>
      <div class="news-date">&#128197; Jan 25,2022</div>
      <p>At vero eos et accusamus et iusto odio dignissiducimumos ducimus qui blanditiis</p>
      <div class="news-more">READ MORE <svg width="13" height="13" viewBox="0 0 13 13"><circle cx="6.5" cy="6.5" r="6.5" fill="#0f3f68"/><path d="M5 3.5l3 3-3 3" stroke="#fff" stroke-width="1.6" fill="none"/></svg></div>
    </article>
    <div class="news-photo-b" role="img" aria-label="Hand on a desk phone with digital network icons"></div>
    <article class="news-card">
      <h3>At vero eos eaccusamu</h3>
      <div class="news-date">&#128197; Jan 25,2022</div>
      <p>At vero eos et accusamus et iusto odio dignissiducimumos ducimus qui blanditiis</p>
      <div class="news-more">READ MORE <svg width="13" height="13" viewBox="0 0 13 13"><circle cx="6.5" cy="6.5" r="6.5" fill="#0f3f68"/><path d="M5 3.5l3 3-3 3" stroke="#fff" stroke-width="1.6" fill="none"/></svg></div>
    </article>
    <div class="news-photo-c" role="img" aria-label="Professional working at a computer in a dark operations room"></div>
    <article class="news-card">
      <h3>At vero eos eaccusamu</h3>
      <div class="news-date">&#128197; Jan 25,2022</div>
      <p>At vero eos et accusamus et iusto odio dignissiducimumos ducimus qui blanditiis</p>
      <div class="news-more">READ MORE <svg width="13" height="13" viewBox="0 0 13 13"><circle cx="6.5" cy="6.5" r="6.5" fill="#0f3f68"/><path d="M5 3.5l3 3-3 3" stroke="#fff" stroke-width="1.6" fill="none"/></svg></div>
    </article>
  </div>
</section>

<footer>
  <div class="abs contact"></div>
  <h2 class="abs contact-title">CONTACT US</h2>
  <p class="abs contact-label" style="left:143px;top:3242px">Get In Touch:</p>
  <div class="field" style="left:145px;top:3285px;width:266px;height:30px">Name :</div>
  <div class="field" style="left:422px;top:3285px;width:266px;height:30px">Phone :</div>
  <div class="field" style="left:145px;top:3326px;width:543px;height:30px">Email :</div>
  <div class="field" style="left:145px;top:3366px;width:543px;height:66px">Message :</div>
  <div class="abs submit">SUBMIT</div>

  <p class="abs contact-label" style="left:757px;top:3242px">Contact Information</p>
  <div class="abs info" style="top:3278px">
    <span class="info-icon"><svg width="14" height="16" viewBox="0 0 14 16"><path d="M7 15s5-5 5-9A5 5 0 0 0 2 6c0 4 5 9 5 9z" fill="none" stroke="#fff" stroke-width="1.5"/><circle cx="7" cy="6" r="1.8" fill="#fff"/></svg></span>
    <span>123,equi nesciunt eque porro<br>quisquamrcitatione</span>
  </div>
  <div class="abs info" style="top:3331px">
    <span class="info-icon"><svg width="14" height="14" viewBox="0 0 14 14"><path d="M3 1l3 3-2 2c1 2 2 3 4 4l2-2 3 3-2 2C6 13 1 8 1 3z" fill="#fff"/></svg></span>
    <span>Phone : +1 555 014 2290</span>
  </div>
  <div class="abs info" style="top:3376px">
    <span class="info-icon"><svg width="14" height="11" viewBox="0 0 14 11"><rect x="0.5" y="0.5" width="13" height="10" rx="1" fill="#fff"/><path d="M1 1l6 5 6-5" stroke="#0f3f68" stroke-width="1.3" fill="none"/></svg></span>
    <span>info@meridalestaffing.com</span>
  </div>
  <div class="abs socials" aria-label="Social links"><i></i><i></i><i></i><i></i><i></i></div>
  <div class="abs live-chat"><span>LIVE CHAT</span></div>
  <div class="abs footer-rule"></div>
  <p class="abs copyright">Copyrights &copy; 2022, Meridale Staffing. All Rights Reserved &nbsp;|&nbsp; Privacy policy</p>
</footer>

</body>
</html>
```